Verodex business card

Business card for sustainable investment company called "Verodex". Verodex is an exchange platform selling carbon credits between buyers and sellers. Carbon Credits are an environmental commodity for reducing global carbon emissions.

the card should obviously have our logo and the theme should be sustainability/environment mixed with a trading platform.

Contact Information for Business Card

Logo, Name, Title, Phone, Email

Colors
0054AA
0677BA
7BADD7
CADEEF
E8F1F8
0094D4
00A9DD
6FCCEA
C7EBF8
E9F6FB
00AB8E
00BBA5
67D7C9
C6EFE9
E9F9F6
59FF00
82FF00
B8FF75
E3FFCB
F4FFEA

```html
<!DOCTYPE html>
<html lang="en">
<head>
<meta charset="utf-8">
<title>Verodex business card</title>
<link rel="stylesheet" href="https://fonts.googleapis.com/css2?family=Montserrat:wght@400;500;600;700&display=swap">
<style>
  :root {
    --backdrop: #2e2f31;
    --navy: #1b2c5c;
    --navy-deep: #13224a;
    --ink: #26324f;
    --sky: #2fb6e6;
    --sky-light: #6fcfe6;
    --blue: #4a7fd0;
    --paper: #ffffff;
  }
  * { margin: 0; padding: 0; box-sizing: border-box; }
  html, body {
    width: 1200px; height: 960px; overflow: hidden;
    background: var(--backdrop);
    font-family: "Montserrat", sans-serif;
  }
  .card {
    position: absolute; left: 250px;
    width: 700px; height: 400px;
    border-radius: 24px; overflow: hidden;
    box-shadow: 0 14px 30px rgba(0,0,0,.45);
  }
  .card-front {
    top: 45px;
    background: linear-gradient(135deg, #24386b 0%, var(--navy) 45%, var(--navy-deep) 100%);
  }
  .card-back { top: 505px; background: var(--paper); }

  .brand { position: absolute; display: flex; align-items: center; gap: 22px; }
  .brand-mark { width: 58px; height: 58px; border-radius: 8px; background: linear-gradient(135deg, var(--sky-light), var(--blue)); }
  .brand-name { font-weight: 600; font-size: 66px; letter-spacing: 1px; line-height: 1; }
  .card-front .brand { left: 150px; top: 165px; }
  .card-front .brand-name { color: var(--paper); }
  .card-back .brand { left: 170px; top: 58px; }
  .card-back .brand-name { color: var(--ink); }

  .wave { position: absolute; inset: 0; width: 700px; height: 400px; }

  .identity { position: absolute; right: 310px; top: 170px; text-align: right; }
  .person-name { font-weight: 700; font-size: 27px; color: var(--navy); letter-spacing: .5px; }
  .person-name .first { color: var(--sky); }
  .person-title { font-weight: 400; font-size: 19px; color: #222; margin-top: 4px; }

  .divider { position: absolute; left: 406px; top: 164px; width: 2px; height: 82px; background: var(--sky); }

  .contacts { position: absolute; left: 422px; top: 164px; list-style: none; }
  .contacts li { display: flex; align-items: center; gap: 9px; font-size: 17px; color: #1a1a1a; height: 27px; }
  .contacts svg { width: 17px; height: 17px; flex: none; }
</style>
</head>
<body>
  <section class="card card-front" aria-label="Card front">
    <div class="brand">
      <span class="brand-mark"></span>
      <span class="brand-name">VERODEX</span>
    </div>
  </section>

  <section class="card card-back" aria-label="Card back">
    <svg class="wave" viewBox="0 0 700 400" aria-hidden="true">
      <defs>
        <linearGradient id="stripeTone" x1="0" y1="0" x2="1" y2="0">
          <stop offset="0" stop-color="#6fcfe6"/>
          <stop offset=".55" stop-color="#2fb6e6"/>
          <stop offset="1" stop-color="#4a6fc8"/>
        </linearGradient>
      </defs>
      <path d="M100,372 C330,368 470,320 580,275 C630,255 670,245 700,242" fill="none" stroke="url(#stripeTone)" stroke-width="9"/>
      <path d="M140,400 C350,396 490,350 600,305 C645,287 675,278 700,276 L700,400 Z" fill="#1b2c5c"/>
    </svg>

    <div class="brand">
      <span class="brand-mark"></span>
      <span class="brand-name">VERODEX</span>
    </div>

    <div class="identity">
      <p class="person-name"><span class="first">DANIEL</span> HARKER</p>
      <p class="person-title">Co-Founder</p>
    </div>

    <div class="divider"></div>

    <ul class="contacts">
      <li>
        <svg viewBox="0 0 24 24"><path fill="#2fb6e6" d="M6.6 10.8a15 15 0 0 0 6.6 6.6l2.2-2.2a1 1 0 0 1 1-.25 11.4 11.4 0 0 0 3.6.57 1 1 0 0 1 1 1V20a1 1 0 0 1-1 1A17 17 0 0 1 3 4a1 1 0 0 1 1-1h3.5a1 1 0 0 1 1 1c0 1.250.2 2.450.57 3.6a1 1 0 0 1-.25 1z"/></svg>
        555-014-2290
      </li>
      <li>
        <svg viewBox="0 0 24 24"><rect x="2" y="5" width="20" height="14" rx="2" fill="#2fb6e6"/><path d="M3 6l9 7 9-7" fill="none" stroke="#fff" stroke-width="1.6"/></svg>
        info@verodex.com
      </li>
      <li>
        <svg viewBox="0 0 24 24"><circle cx="12" cy="12" r="10" fill="#2fb6e6"/><path d="M2 12h20M12 2c3 3 3 17 0 20M12 2c-3 3-3 17 0 20" fill="none" stroke="#fff" stroke-width="1.3"/></svg>
        www.verodex.com
      </li>
    </ul>
  </section>
</body>
</html>
```